Skiing Company Needs A5 28page Skiing Catalogue

ABOUT THE BUSINESS/COMPANY:
- We are a guided skiing company called "Silver Lantern Journeys" and "Kestrel Ridge Alpine Society".

ABOUT THE CATALOGUE:

- We need an A5 28 page catalogue. ALL THE FILES (like photos and logos) are in the zip folders.

- You can look at the 000 KRS Catalog Word Document. Instructions on what text and photos to use are labeled there per Page.

Target Market(s)

Advanced/ Expert Skiers and Snowboarders that are thinking of joining a tour

Industry/Entity Type

Travel Agent

Font styles to use
Serif

Colors
ffffff
ec1f27
0455a3

Requirements
Must have
• NEED a 3mm bleed
• This is included on the 000 KRS Catalog word document
Nice to have
• Our main color is dark blue (just like our logo). Some red is ok but the main focus should be the dark blue.
Should not have
• Words/ Letters in the color red

```html
<!DOCTYPE html>
<html lang="en">
<head>
<meta charset="utf-8">
<title>Catalogue Spread – Evolution of Niseko</title>
<link href="https://fonts.googleapis.com/css2?family=Tinos:ital,wght@0,400;0,700;1,400&display=swap" rel="stylesheet">
<style>
  :root {
    --backdrop: #c8c8c8;
    --paper: #f4f5f9;
    --blue-deep: #2f5ea8;
    --blue-mid: #3f72bb;
    --blue-panel: #3a6ab5;
    --brand-blue: #0455a3;
    --sky-light: #8fb0d8;
    --ink: #1b1b1b;
    --white: #ffffff;
  }
  * { box-sizing: border-box; margin: 0; padding: 0; }
  html, body {
    width: 1200px; height: 789px; overflow: hidden;
    background: var(--backdrop);
    font-family: "Tinos", "Times New Roman", serif;
  }
  .spread {
    position: absolute; left: 63px; top: 14px;
    width: 1074px; height: 760px;
    display: flex;
    box-shadow: 0 6px 18px rgba(0,0,0,.18);
  }
  .page { position: relative; width: 537px; height: 760px; overflow: hidden; }

  /* Left page */
  .page--evolution {
    background: linear-gradient(180deg, var(--blue-deep) 0%, var(--blue-mid) 40%, var(--sky-light) 60%);
    color: var(--white);
  }
  .landscape-photo {
    position: absolute; left: 0; right: 0; bottom: 0; height: 330px;
    background: linear-gradient(180deg, #9bb7d9 0%, #c9d6e6 25%, #e8edf3 40%, #8a97a8 75%, #4a5566 100%);
  }
  .title-pill {
    display: inline-block;
    border: 1.5px solid currentColor;
    border-radius: 20px;
    padding: 4px 22px 5px 14px;
    font-size: 20px; font-weight: 700;
    letter-spacing: .3px;
  }
  .page--evolution .title-pill { position: absolute; left: 34px; top: 34px; }
  .body-copy {
    font-size: 12px; line-height: 1.22;
    text-align: justify;
  }
  .body-copy p + p { margin-top: 12px; }
  .page--evolution .body-copy { position: absolute; left: 34px; right: 34px; top: 82px; }

  /* Right page */
  .page--fatalities { background: var(--paper); color: var(--ink); }
  .page--fatalities .title-pill {
    position: absolute; left: 34px; top: 34px;
    color: var(--brand-blue); font-weight: 400; font-size: 19px;
  }
  .page--fatalities .body-copy { position: absolute; left: 34px; right: 34px; top: 78px; }
  .note {
    font-size: 10.5px; font-weight: 700; line-height: 1.2; margin-top: 8px;
  }
  .portrait-photo {
    position: absolute; left: 0; top: 348px; width: 300px; bottom: 0;
    background: linear-gradient(180deg, #dfe3e8 0%, #c4ccd6 45%, #8d8a6a 80%, #6e6a3c 100%);
  }
  .tribute-panel {
    position: absolute; left: 300px; right: 0; top: 398px; bottom: 0;
    background: var(--blue-panel);
  }
  .tribute-frame {
    position: absolute; left: 22px; right: 22px; top: 40px; height: 240px;
    border: 1px solid var(--white);
    color: var(--white);
    text-align: center;
    display: flex; flex-direction: column; justify-content: center; align-items: center;
  }
  .tribute-we { font-size: 58px; line-height: .95; }
  .tribute-miss { font-size: 24px; letter-spacing: 1px; margin-bottom: 10px; }
  .tribute-quote { font-size: 30px; line-height: .6; }
  .tribute-name { font-size: 34px; letter-spacing: 1px; line-height: 1.1; }
</style>
</head>
<body>
<div class="spread">
  <section class="page page--evolution">
    <h2 class="title-pill">Evolution of Niseko</h2>
    <div class="body-copy">
      <p>With increased numbers of foreign travelers, resorts around Hokkaido have also undergone many changes. Along with new lifts and developments, many resorts have now instituted a long overdue open gate/backcountry policy to help satisfy the undeniable and rapidly increasing backcountry skier/boarder market. Each resort has a slightly different twist, so please be sure to check in with us or the resort to find out the latest. While Northpeak Resorts has recently invested heavily into the growing beginner Asian market with 4 new lifts, little has been dedicated to the hardcore powder junkies. Please be sure to let the local tourism board that you (like us) want the more and ask them when they will finally open and control Yunosawa and Harunotaki.</p>
      <p>Despite our consistent weather and relatively stable snowpack, with all this wind and snowfall, accidents DO happen in Hokkaido. Since 1937, there has been 103 individuals that have reported an encounter with an avalanche in Northpeak Resorts, and unfortunately 15 people have lost their lives. Given the negative press and connotation of a backcountry "accident" we suspect there have been MANY more that have gone unreported. Please be careful out there and be prepared for self rescue no matter where you are.</p>
    </div>
    <div class="landscape-photo" role="img" aria-label="Aerial photo of a snow-covered volcano rising above a winter valley under blue sky"></div>
  </section>

  <section class="page page--fatalities">
    <h2 class="title-pill">Fatalities in Niseko</h2>
    <div class="body-copy">
      <p>On February 25th Niseko lost a legend. Tom Arlen, loving husband, father, mountain and rafting guide lost his life to an avalanche on the southeast face of Haru-no-taki. The snow was incredible that day, but the crowds and lift lines were even more so. When you use a lift and/or you're in competition for fresh powder, decisions get made much faster as was the case on that very day. People enter these areas because they offer the steepest and best fall-line riding in the area and they are so easily accessed. Simply out, people duck these ropes because these areas never open. If these areas were controlled and managed, we believe that people would wait and locals would self police and strongly enforce these policies. If you give advanced skiers and boarders the opportunity to actually ski these areas, they will respect you back and follow the rules. 4 years ago we lost a wonderful neighbor and father of three when he skied into a fresh glide crack in the Yunosawa area. Had this area been managed, he may still be with us today. Let's not let these losses go in vein. Together we can make positive change happen.</p>
      <p class="note">( Note: SLJ and KRS are trying to make a positive change and this is why we asking all of guests to follow the current rules.)</p>
    </div>
    <div class="portrait-photo" role="img" aria-label="Snow-covered rider in goggles and yellow jacket among frosted trees"></div>
    <div class="tribute-panel">
      <div class="tribute-frame">
        <span class="tribute-we">WE</span>
        <span class="tribute-miss">MISS YOU</span>
        <span class="tribute-quote">“</span>
        <span class="tribute-name">TOMCAT</span>
        <span class="tribute-quote">”</span>
      </div>
    </div>
  </section>
</div>
</body>
</html>
```